Allied Health team of Physiotherapists & Occupational Therapists seek a business card design

We have our new logo, we now need our new business cards and stationary. Tidewell: Oedema & Family Clinic is seeking a generic card design to represent our whole team and individual cards for each therapist that incorporates our new logo to communicate our holistic approach that is calming, nuturing, supportive and welcoming.
Our Physiotherapists and Occupational Therapists assess, treat and provide education for people who are at risk of or who have lymphoedema. This is often as a result of treatment for cancer. We provide pre-operative and post-operative management and cancer rehabilitation in our Pilates studio. Our team also consists of Physiotherapists who have a strong interest in pelvic floor and continence management for both men and women.

Target Market(s)

Mainly women health conscious

Industry/Entity Type

Allied Health: Physiotherapy / Occupational Therapy

Contact Information for Business Card

Address: 14 Gallivant Ave Marlow Bay 3188 Phone: 84316570 fax: 8431 6578 Email: info@tidewellcareservices.com.au Website: tidewellcareservices.com.au Facebook address: facebook.com/TidewellOedemaAndFamilyCareClinic. Room to write appointments. Individual cards need to have name, office email and individual email and professional details

Requirements
Must have
• Logo as per uploaded documents

```html
<!DOCTYPE html>
<html lang="en">
<head>
<meta charset="utf-8">
<title>Tidewell Business Card</title>
<link rel="stylesheet" href="https://fonts.googleapis.com/css2?family=Barlow:ital,wght@0,400;0,500;0,600;1,500&family=Philosopher:wght@700&display=swap">
<style>
  :root {
    --bg: #131416;
    --cream: #fffbd6;
    --peach: #fbb07f;
    --peach-light: #fdd2ad;
    --sage: #c1cbbf;
    --ink: #2b2a27;
    --ink-soft: #4a4843;
    --on-peach: #fffbe2;
  }
  * { margin: 0; padding: 0; box-sizing: border-box; }
  html, body { width: 1200px; height: 886px; overflow: hidden; background: var(--bg); }
  body { position: relative; font-family: "Barlow", sans-serif; }

  .card {
    position: absolute;
    width: 446px; height: 255px;
    overflow: hidden;
    box-shadow: 0 30px 60px rgba(0,0,0,.55);
  }
  .card--front { left: 223px; top: 142px; background: var(--cream); }
  .card--back  { left: 531px; top: 488px; background: var(--peach); }

  .brand-panel {
    position: absolute; left: 0; top: 0;
    width: 155px; height: 221px;
    border-bottom-right-radius: 8px;
    z-index: 2;
    display: flex; align-items: center; justify-content: center;
  }
  .brand-tab {
    position: absolute; left: 0; top: 214px;
    width: 135px; height: 24px;
    border-bottom-right-radius: 8px;
    z-index: 1;
  }
  .card--front .brand-panel { background: var(--peach); }
  .card--front .brand-tab   { background: var(--sage); }
  .card--back .brand-panel  { background: var(--sage); }
  .card--back .brand-tab    { background: var(--peach-light); }

  .brand-mark {
    width: 118px; height: 118px;
    border: 1.5px solid var(--on-peach);
    border-radius: 50%;
    display: flex; align-items: center; justify-content: center;
  }
  .brand-name {
    font-family: "Barlow", sans-serif;
    font-weight: 500; font-size: 24px;
    color: var(--on-peach);
  }

  .profile { position: absolute; left: 190px; top: 42px; color: var(--ink); }
  .profile__name {
    font-family: "Philosopher", sans-serif;
    font-weight: 700; font-size: 19px; line-height: 22px;
  }
  .profile__role {
    font-style: italic; font-weight: 500; font-size: 12.5px;
    color: var(--ink-soft); margin-top: 3px;
  }
  .profile__quals {
    list-style: none; margin-top: 12px;
    font-size: 10.5px; line-height: 15px; color: var(--ink-soft);
  }
  .profile__focus {
    list-style: none; margin-top: 36px;
    font-weight: 600; font-size: 10.5px; line-height: 17px;
  }

  .contact { position: absolute; left: 190px; top: 37px; right: 0; color: var(--on-peach); }
  .contact__item {
    display: flex; align-items: center; gap: 5px;
    height: 17.5px; font-size: 12px; white-space: nowrap;
  }
  .contact__item--phone { font-size: 13px; letter-spacing: 1px; }
  .contact__item--small { font-size: 10.5px; }
  .contact__icon { width: 13px; height: 13px; flex: none; }
  .contact__rule { height: 1px; background: var(--on-peach); opacity: .7; margin: 10px 0 8px; }
  .appointment {
    position: absolute; left: 210px; top: 199px;
    font-weight: 500; font-size: 12.5px; color: var(--on-peach);
    display: flex; align-items: baseline; gap: 4px;
  }
  .appointment__line { width: 84px; border-bottom: 1px dotted var(--on-peach); }
</style>
</head>
<body>

  <section class="card card--front" aria-label="Business card front">
    <div class="brand-panel">
      <div class="brand-mark"><span class="brand-name">Tidewell</span></div>
    </div>
    <div class="brand-tab"></div>
    <div class="profile">
      <h1 class="profile__name">Maren Holt</h1>
      <p class="profile__role">Physiotherapist</p>
      <ul class="profile__quals">
        <li>B. Physio (Hons), B.App.Sci. (Human Movement/Psych)</li>
        <li>Post Grad Certif. Exercise for Women</li>
        <li>Post Grad Certif. Continence &amp; Pelvic Floor</li>
        <li>Rehabilitation</li>
      </ul>
      <ul class="profile__focus">
        <li>Lymphoedema &amp; Oncology Rehabilitation</li>
        <li>Continence &amp; Pelvic Floor</li>
      </ul>
    </div>
  </section>

  <section class="card card--back" aria-label="Business card back">
    <div class="brand-panel">
      <div class="brand-mark"><span class="brand-name">Tidewell</span></div>
    </div>
    <div class="brand-tab"></div>
    <div class="contact">
      <div class="contact__item contact__item--phone">
        <svg class="contact__icon" viewBox="0 0 14 14" fill="none" stroke="#fffbe2" stroke-width="1"><circle cx="7" cy="7" r="6.3"/><path d="M4.6 4c.6 2.6 2.2 4.3 5 5.2l.6-1.2-1.4-.8-.6.6C7.3 7.3 6.6 6.6 6.1 5.7l.6-.6-.8-1.4z"/></svg>
        8431 6570
      </div>
      <div class="contact__item contact__item--phone">
        <svg class="contact__icon" viewBox="0 0 14 14" fill="none" stroke="#fffbe2" stroke-width="1"><circle cx="7" cy="7" r="6.3"/><rect x="4" y="5.5" width="6" height="4"/><path d="M5 5.5V3.8h4v1.7"/></svg>
        8431 6578
      </div>
      <div class="contact__item">
        <svg class="contact__icon" viewBox="0 0 14 14" fill="none" stroke="#fffbe2" stroke-width="1"><circle cx="7" cy="7" r="6.3"/><rect x="3.8" y="4.8" width="6.4" height="4.4"/><path d="M3.8 4.8L7 7.3l3.2-2.5"/></svg>
        info@tidewellcareservices.com.au
      </div>
      <div class="contact__item contact__item--small">
        <svg class="contact__icon" viewBox="0 0 14 14" fill="none" stroke="#fffbe2" stroke-width="1"><circle cx="7" cy="7" r="6.3"/></svg>
        TidewellOedemaAndFamilyCareClinic
      </div>
      <div class="contact__rule"></div>
      <div class="contact__item">
        <svg class="contact__icon" viewBox="0 0 14 14" fill="none" stroke="#fffbe2" stroke-width="1"><circle cx="7" cy="7" r="6.3"/><circle cx="7" cy="7" r="3.4"/><path d="M3.6 7h6.8M7 3.6c-1.4 2-1.4 4.8 0 6.8M7 3.6c1.4 2 1.4 4.8 0 6.8"/></svg>
        tidewellcareservices.com.au
      </div>
      <div class="contact__item">
        <svg class="contact__icon" viewBox="0 0 14 14" fill="none" stroke="#fffbe2" stroke-width="1"><circle cx="7" cy="7" r="6.3"/><path d="M7 10.6S4.6 7.8 4.6 6a2.4 2.4 0 0 1 4.8 0c0 1.8-2.4 4.6-2.4 4.6z"/><circle cx="7" cy="6" r=".8"/></svg>
        14 Gallivant Ave, Marlow Bay 3188
      </div>
    </div>
    <div class="appointment">
      <span>Next Appointment</span><span class="appointment__line"></span>
    </div>
  </section>

</body>
</html>
```